Flyer Promoting Dental Benefit Program

I want to promote a dental benefit program to my patients that do not have dental insurance. This flyer would be posted in our waiting room and where people make payments. The goal would be to get those interested to request more information and enroll in the program. I have a card that will be issued that has a logo. Theflyer and card should feel congruent. I've uploaded a file with a copy of that card.
The plan costs $290/person. It includes 2 cleanings, exams, and x-rays. It also includes a 20% discount off of our standard fees. The plan or membership lasts for one year. It is only available to those without insurance. It is also important to let people know that this is not insurance (some kind of a disclaimer).
Updates
This plan is only available to patients at my office. The contact information is: Harborview Dental, 2718 West 4600 North Suite 209, Salt Lake City, Utah 84157. (801) 563-9071. info@harborviewdental-example.com. It is not necessary to include contact information as this flyer will be used as in-office promotion.
Target Market(s)
Those without dental insurance, but have resources to afford dental care.
Industry/Entity Type
Insurance
Look and feel
Each slider illustrates characteristics of the customer's brand and the style your logo design should communicate.

```html
<!DOCTYPE html>
<html lang="en">
<head>
<meta charset="utf-8">
<title>Dental Benefit Plan Flyer</title>
<link rel="stylesheet" href="https://fonts.googleapis.com/css2?family=Jost:ital,wght@0,300;0,400;0,500;0,700;0,800;1,500&display=swap">
<style>
  :root {
    --backdrop: #3a3a3a;
    --paper: #ffffff;
    --green: #0e8b3a;
    --green-deep: #17663a;
    --green-light: #8cc63f;
    --yellow: #f4e400;
    --grass-1: #d8ea7a;
    --grass-2: #7fb82e;
    --grass-3: #4e8f1f;
  }
  * { margin: 0; padding: 0; box-sizing: border-box; }
  html, body {
    width: 1200px; height: 750px; overflow: hidden;
    background: var(--backdrop);
    font-family: "Jost", "Futura", sans-serif;
  }
  .flyer {
    position: absolute; left: 330px; top: 25px;
    width: 540px; height: 700px;
    background: var(--paper);
    overflow: hidden;
  }
  .flyer-shapes { position: absolute; inset: 0; }
  .brand {
    position: absolute; right: 28px; top: 30px;
    display: flex; align-items: center; gap: 8px;
    color: var(--green-deep); font-weight: 700; font-size: 20px;
    letter-spacing: 0.5px;
  }
  .brand-dot { width: 30px; height: 30px; border-radius: 50%; background: var(--green-light); }
  .phone {
    position: absolute; right: 28px; top: 112px;
    color: #fff; font-weight: 700; font-size: 16px; letter-spacing: 0.5px;
  }
  .headline {
    position: absolute; right: 30px; top: 190px;
    text-align: right; color: var(--green-deep); line-height: 0.92;
    text-transform: uppercase;
  }
  .headline .line-light { font-weight: 400; font-size: 42px; display: block; }
  .headline .line-bold { font-weight: 800; font-size: 50px; color: var(--green); display: block; }
  .headline .line-small { font-weight: 400; font-size: 30px; display: block; }
  .disclaimer {
    position: absolute; left: 22px; top: 440px; width: 150px;
    color: var(--green); font-size: 11px; line-height: 1.35;
  }
  .disclaimer strong { font-weight: 700; }
  .offer {
    position: absolute; left: 260px; top: 430px; width: 260px;
    color: #fff;
  }
  .price { color: var(--yellow); font-weight: 800; font-size: 66px; line-height: 1; letter-spacing: -1px; }
  .price .per { font-size: 18px; font-weight: 500; font-style: italic; letter-spacing: 0; }
  .offer-rule { height: 2px; background: var(--yellow); margin: 6px 0 8px; width: 220px; }
  .offer-title { font-size: 17px; font-weight: 400; }
  .offer-title strong { font-weight: 700; }
  .benefits { list-style: none; margin-top: 4px; }
  .benefits li {
    display: flex; align-items: center; gap: 6px;
    color: var(--green-light); font-size: 17px; line-height: 1.35;
  }
  .tick { width: 14px; height: 12px; flex: none; }
</style>
</head>
<body>
  <main class="flyer">
    <svg class="flyer-shapes" viewBox="0 0 540 700" width="540" height="700" aria-hidden="false">
      <defs>
        <linearGradient id="grass" x1="0" y1="0" x2="1" y2="1">
          <stop offset="0" stop-color="var(--grass-3)"/>
          <stop offset="0.45" stop-color="var(--grass-2)"/>
          <stop offset="1" stop-color="var(--grass-1)"/>
        </linearGradient>
      </defs>
      <!-- photo area -->
      <path role="img" aria-label="Photo of a smiling woman lying in fresh green grass"
            d="M0,0 H250 C330,50 430,90 540,100 V420 C470,395 410,330 300,310 C200,292 100,300 0,250 Z"
            fill="url(#grass)"/>
      <!-- top-right band along the curve -->
      <path d="M250,0 C330,50 430,90 540,100 V112 C430,102 325,62 240,0 Z" fill="var(--yellow)"/>
      <path d="M290,98 C380,118 460,124 540,122 V144 C450,146 370,138 290,112 Z" fill="var(--green)"/>
      <!-- lower yellow field with green edge -->
      <path d="M0,262 C100,312 200,308 300,328 C400,350 470,425 540,448 V700 H0 Z" fill="var(--green)"/>
      <path d="M0,282 C100,330 200,324 300,342 C400,362 470,436 540,458 V700 H0 Z" fill="var(--yellow)"/>
      <!-- offer circle -->
      <circle cx="395" cy="555" r="196" fill="var(--yellow)"/>
      <circle cx="395" cy="555" r="186" fill="var(--green-light)"/>
      <circle cx="395" cy="555" r="172" fill="var(--green)"/>
    </svg>

    <div class="brand"><span class="brand-dot"></span><span>Harborview Dental</span></div>
    <div class="phone">CALL (801) 563-9071</div>

    <h1 class="headline">
      <span class="line-light">Dental</span>
      <span class="line-bold">Benefit</span>
      <span class="line-small">Plan</span>
    </h1>

    <p class="disclaimer">* <strong>The Dental Benefit Plan</strong> is an annual plan and it is ONLY available to those without insurance.</p>

    <section class="offer">
      <div class="price">$290<span class="per">/person</span></div>
      <div class="offer-rule"></div>
      <p class="offer-title"><strong>Dental Benefit Plan</strong>* includes:</p>
      <ul class="benefits">
        <li><svg class="tick" viewBox="0 0 14 12"><path d="M1,6 L5,10 L13,1" stroke="#fff" stroke-width="2.6" fill="none"/></svg>2 Cleaning Sessions</li>
        <li><svg class="tick" viewBox="0 0 14 12"><path d="M1,6 L5,10 L13,1" stroke="#fff" stroke-width="2.6" fill="none"/></svg>Teeth Examinations</li>
        <li><svg class="tick" viewBox="0 0 14 12"><path d="M1,6 L5,10 L13,1" stroke="#fff" stroke-width="2.6" fill="none"/></svg>X-Rays</li>
        <li><svg class="tick" viewBox="0 0 14 12"><path d="M1,6 L5,10 L13,1" stroke="#fff" stroke-width="2.6" fill="none"/></svg>20% Off Standard Fee</li>
      </ul>
    </section>
  </main>
</body>
</html>
```